Flyer for Compassion training days

I need a A5-size, single-sided flyer design for my training days. They are weekends in a blend of Compassionate Communication and Buddhist teachings called Gentlewise Dialogue. The logo for Gentlewise that should be included.
The flyer needs room for 1) course title, 2) course dates, location & price, 3) course description, 4) booking info, 5) my picture & short bio, and 6) the gentlewise.co website (yes, it is 'co' and not 'com).
Updates

Target Market(s)

Women 35-65 years, well-educated, spiritually minded. May have interests like yoga and meditation.

Industry/Entity Type

Health And Wellness

Font styles to use
Sans Serif
Other font styles liked:
• Blue Plaque, Josefina are both great

Colors
fbf289
fdf9cf
cfeae6
33b8a4

Requirements
Must have
• The Gentlewise logo; my picture.
• Elegance. Calm and expansive feel.
• The poster provided in the project files shows you the kind of information I need to include.
• Colours -- greens and yellows, but the options on craft plaza are not quite the right shades.
• The logo colour can be changed.
Nice to have
• Classy (but not cliche) image associated with Buddhism; gentle curves similar to those on the business card (see project files).
Should not have
• Dark background. Busy, loud design. Overly 'swirly' design. Images that I have to buy separately.

```html
<!DOCTYPE html>
<html lang="en">
<head>
<meta charset="utf-8">
<title>Gentlewise Dialogue – Core Course Flyer</title>
<link href="https://fonts.googleapis.com/css2?family=Josefin+Sans:wght@400;600;700&display=swap" rel="stylesheet">
<style>
  :root{
    --teal:#2bab94;
    --teal-dark:#1f9a84;
    --blue:#4a86c6;
    --ink:#2e2e2e;
    --ink-soft:#3a3a3a;
    --rule:#a9a9a9;
    --paper:#f6f6f5;
    --page:#e4e6e2;
    --pill-dark:#2a2a2a;
  }
  *{box-sizing:border-box;margin:0;padding:0}
  html,body{width:1200px;height:1199px;overflow:hidden;background:var(--page)}
  body{font-family:"Josefin Sans",sans-serif;color:var(--ink)}
  .flyer{
    position:absolute;left:328px;top:55px;width:761px;height:1078px;overflow:hidden;
    background:radial-gradient(ellipse at 40% 55%,#ffffff 0%,var(--paper) 55%,#ecebea 100%);
    box-shadow:0 6px 18px rgba(0,0,0,.18);
  }
  .flyer > *{position:absolute}
  .header-art{left:0;top:0;width:761px;height:320px}
  .brand-mark{left:535px;top:195px;display:flex;align-items:center;gap:8px;
    font-weight:700;font-size:22px;color:var(--teal)}
  .brand-mark .dot{width:16px;height:16px;border-radius:50%;background:var(--teal)}
  .equation{left:60px;top:236px;width:470px;text-align:center;color:var(--teal);
    font-weight:600;font-size:29px;line-height:32px}
  .course-title{left:62px;top:304px;font-size:66px;font-weight:400;color:var(--ink-soft);letter-spacing:.5px;white-space:nowrap}
  .course-pill{left:45px;top:385px;width:190px;height:50px;background:var(--teal);
    color:#fff;font-size:29px;font-weight:400;padding:12px 0 0 20px;border-radius:16px 4px 16px 4px}
  .course-facts{left:67px;top:455px;font-size:21px;font-weight:600;line-height:28px;color:var(--ink)}
  .intro{left:257px;top:385px;width:450px;font-size:17px;line-height:24px;color:var(--ink-soft)}
  .choose{left:330px;top:489px;display:flex;align-items:center;gap:12px;color:var(--teal);font-size:18px;font-weight:600}
  .choose i{display:block;width:36px;height:3px;background:var(--teal)}
  .explore-head{left:257px;top:518px;font-size:21px;font-weight:600;color:var(--ink-soft)}
  .topics{left:262px;top:556px;width:450px;list-style:none;font-size:17px;font-weight:600;line-height:22px}
  .topics li{position:relative;padding-left:15px;margin-bottom:6px}
  .topics li::before{content:"";position:absolute;left:0;top:8px;width:4px;height:4px;border-radius:50%;background:var(--blue)}
  .dividers{left:0;top:460px;width:761px;height:320px}
  .side-mark{left:68px;top:680px;display:flex;align-items:center;gap:8px;font-size:22px;font-weight:600;color:var(--teal)}
  .side-mark .dot{width:14px;height:14px;border:2px solid var(--teal);border-radius:50%}
  .website{left:39px;top:773px;font-size:23px;font-weight:700;color:var(--ink)}
  .audience{left:257px;top:708px;width:450px;font-size:17px;line-height:23.5px;color:var(--ink-soft)}
  .portrait{left:36px;top:825px;width:196px;height:196px;border-radius:50%;border:3px solid var(--pill-dark);
    background:radial-gradient(circle at 50% 40%,#c9bfb2 0%,#8a7b6a 45%,#4c4035 100%)}
  .tag{height:28px;padding:5px 14px 0;font-size:19px;font-weight:600;color:#fff;border-radius:10px 3px 10px 3px}
  .tag-booking{left:257px;top:838px;background:var(--teal)}
  .tag-facilitator{left:257px;top:891px;background:var(--pill-dark)}
  .booking-text{left:383px;top:840px;font-size:18px;font-weight:600;line-height:24px}
  .booking-text span{color:var(--teal-dark)}
  .bio{left:273px;top:900px;width:440px;font-size:17px;line-height:23.5px;color:var(--ink-soft);text-indent:103px}
  .coaching{left:273px;top:1000px;font-size:17px;font-weight:600}
</style>
</head>
<body>
  <main class="flyer">
    <svg class="header-art" viewBox="0 0 761 320" aria-hidden="false">
      <defs>
        <linearGradient id="sky" x1="0" y1="0" x2="1" y2="1">
          <stop offset="0" stop-color="#e9ddd0"/>
          <stop offset=".45" stop-color="#c9c5bd"/>
          <stop offset="1" stop-color="#f1e6dc"/>
        </linearGradient>
      </defs>
      <path role="img" aria-label="Photograph of a water droplet hanging from a bare twig" fill="url(#sky)"
        d="M0 0H761V180C700 160 640 130 560 120C470 110 380 150 260 170C170 185 90 160 0 135Z"/>
      <path fill="var(--teal)" d="M0 135C90 160 170 185 260 170C380 150 470 110 560 120C640 130 700 160 761 190V205C700 172 640 145 560 137C470 128 380 168 260 186C165 200 85 175 0 152Z"/>
      <path fill="var(--blue)" d="M414 25C440 90 520 120 600 135C660 148 720 170 761 188V196C710 178 650 160 590 148C500 130 430 95 414 25Z"/>
    </svg>

    <div class="brand-mark"><span class="dot"></span>Gentlewise</div>

    <p class="equation">Mindfulness + Kindness +<br>Compassionate Communication =</p>
    <h1 class="course-title">Gentlewise Dialogue</h1>

    <div class="course-pill">Core Course</div>
    <p class="course-facts">11-12 Dec<br>Linden Hall Centre,<br>Edinburgh<br>£125/100</p>

    <p class="intro">Gentlewise Dialogue can help you increase awareness &amp; compassion in everyday speech (with yourself &amp; others), better understand your own patterns, and build resilience to challenging situations.</p>
    <div class="choose"><i></i>Choose from:<i></i></div>
    <h2 class="explore-head">In this 2-day Core Course, we’ll explore</h2>

    <svg class="dividers" viewBox="0 0 761 320" aria-hidden="true">
      <path fill="none" stroke="var(--rule)" stroke-width="2"
        d="M0 88C40 88 60 120 80 150C100 175 140 175 160 160C190 140 215 85 300 85H690C730 85 755 60 761 30"/>
      <path fill="none" stroke="var(--rule)" stroke-width="2"
        d="M0 230C40 230 60 205 80 185C100 168 140 165 170 180C200 195 215 225 250 228C300 232 380 232 690 232C730 232 755 260 761 300"/>
    </svg>

    <ul class="topics">
      <li>Compassionate Communication;</li>
      <li>Buddhist teachings on Right Speech, loving-kindness, Right Effort, and more;</li>
      <li>mindfulness practices;</li>
      <li>choices available to us in our everyday speech.</li>
    </ul>

    <div class="side-mark"><span class="dot"></span>Gentlewise</div>
    <p class="website">www.gentlewise.co</p>

    <p class="audience">This workshop will be of interest if you’d like to improve personal and/or professional relationships.&nbsp; Open to all, best suited to those with at least 1 year’s experience with Mindfulness,&nbsp; Buddhism, or Compassionate Communication / NVC.</p>

    <div class="portrait" role="img" aria-label="Portrait photograph of the course facilitator"></div>

    <div class="tag tag-booking">booking</div>
    <p class="booking-text">Book online at TicketNest or<br>write <span>marisol@gentlewise.co</span></p>

    <div class="tag tag-facilitator">facilitator</div>
    <p class="bio">Marisol Hartwell is an experienced group facilitator, having worked with a range of organisations and presented at a number of festivals &amp; conferences.</p>
    <p class="coaching">Marisol offers coaching in Gentlewise Dialogue.</p>
  </main>
</body>
</html>
```